Business card por a urban DJ, up scale audience target

Need a sober design, modern, conservative colors but i can consider some options, y play rnb, hip hop, EDM and top40.

Business card for contact and personal info, double sided, use logo attrached please; im 42 so i need a card acording to my age an target audience.

Target Market(s)

Adult people, up scale audience

Industry/Entity Type

Music Download

Contact Information for Business Card

Cel (318) 4207265518 www.lumadrift.com

Requirements
Must have
• open mind
Nice to have
• open mind
Should not have
• DJ

```html
<!DOCTYPE html>
<html lang="en">
<head>
<meta charset="utf-8">
<title>Marcus Hale – Business Card</title>
<link href="https://fonts.googleapis.com/css2?family=Montserrat:wght@400;600;800&display=swap" rel="stylesheet">
<style>
  :root {
    --page-bg: #e9e7e3;
    --card-white: #ffffff;
    --ink-dark: #2e2e2e;
    --ink-mid: #6b6b6b;
    --band-dark: #262626;
    --band-grey: #8a8a8a;
    --back-grey: #8c8c8c;
    --rule: #cfcfcf;
  }
  * { margin: 0; padding: 0; box-sizing: border-box; }
  html, body {
    width: 1200px; height: 950px; overflow: hidden;
    background: var(--page-bg);
    font-family: "Montserrat", Arial, sans-serif;
  }
  .sheet {
    position: relative; width: 1200px; height: 950px;
  }
  .card {
    position: absolute; left: 250px; width: 700px; height: 400px;
    box-shadow: 0 6px 18px rgba(0,0,0,0.18);
  }
  .card--front { top: 50px; background: var(--card-white); }
  .card--back { top: 500px; background: var(--back-grey); }

  .edge-band {
    position: absolute; top: 0; right: 0; width: 56px; height: 100%;
    background: var(--band-dark);
  }
  .edge-band__accent {
    position: absolute; top: 0; left: 0; width: 100%; height: 36%;
    background: var(--band-grey);
  }

  .brand {
    position: absolute; left: 70px; top: 0; height: 100%; width: 250px;
    display: flex; align-items: center; gap: 14px;
  }
  .brand__mark {
    width: 22px; height: 22px; background: var(--ink-dark);
  }
  .brand__name {
    font-weight: 800; font-size: 64px; letter-spacing: 4px;
    color: var(--ink-dark); line-height: 1;
  }

  .divider {
    position: absolute; left: 330px; top: 110px; width: 1px; height: 180px;
    background: var(--rule);
  }

  .details {
    position: absolute; left: 362px; top: 118px;
  }
  .details__name {
    font-weight: 600; font-size: 26px; color: var(--ink-dark);
    letter-spacing: 0.5px;
  }
  .details__title {
    font-weight: 400; font-size: 16px; color: var(--ink-mid);
    letter-spacing: 0.5px; margin-top: 4px;
  }
  .details__contacts {
    list-style: none; margin-top: 30px;
  }
  .contact {
    display: flex; align-items: center; gap: 10px;
    font-size: 16px; color: var(--ink-dark); margin-bottom: 10px;
  }
  .contact svg { width: 16px; height: 16px; flex: none; }
</style>
</head>
<body>
<main class="sheet">
  <section class="card card--front" aria-label="Business card front">
    <div class="brand">
      <span class="brand__mark"></span>
      <span class="brand__name">LUMA</span>
    </div>
    <div class="divider"></div>
    <div class="details">
      <h1 class="details__name">MARCUS HALE</h1>
      <p class="details__title">CEO/FOUNDER</p>
      <ul class="details__contacts">
        <li class="contact">
          <svg viewBox="0 0 16 16" aria-hidden="true">
            <rect x="3" y="1" width="10" height="14" rx="1.5" fill="none" stroke="#2e2e2e" stroke-width="1.6"/>
            <line x1="6.5" y1="12.5" x2="9.5" y2="12.5" stroke="#2e2e2e" stroke-width="1.4"/>
          </svg>
          <span>(318) 4207265518</span>
        </li>
        <li class="contact">
          <svg viewBox="0 0 16 16" aria-hidden="true">
            <circle cx="8" cy="8" r="7" fill="#2e2e2e"/>
            <ellipse cx="8" cy="8" rx="3" ry="7" fill="none" stroke="#fff" stroke-width="1"/>
            <line x1="1" y1="8" x2="15" y2="8" stroke="#fff" stroke-width="1"/>
          </svg>
          <span>www.lumadrift.com</span>
        </li>
      </ul>
    </div>
    <div class="edge-band"><div class="edge-band__accent"></div></div>
  </section>

  <section class="card card--back" aria-label="Business card back"></section>
</main>
</body>
</html>
```